Satchel & Sundial needs new business card design

I need a new business card design. I'm looking for out-of-the-box design which represents the freedom of being a location independent entrepreneur.
I offer coaching, retreats and trips.
I would like to see designs with and without the photo.
Colors I use are black (#000000), green (#25A796) and brown (#D7C38C)
Website satchelandsundial.example

Target Market(s)

location independent entrepreneurs, digital nomads, people looking to swap the 9 to 5 for a lifestyle business

Industry/Entity Type

Business

Contact Information for Business Card

Dorota Falkner
Your Lifestyle Business Coach, Retreat & Trip Leader
http://satchelandsundial.example
hello@satchelandsundial.example
Live a life you don't need a holiday from

Font styles to use
Serif
Sans Serif

Requirements
Must have
• One side should contain only the logo. I would also consider having the "Live a life you don't need a holiday from" on that side too (depending on how it looks)
• Please show both sides on the designs.

```html
<!DOCTYPE html>
<html lang="en">
<head>
<meta charset="utf-8">
<title>Satchel &amp; Sundial — Business Card</title>
<link rel="stylesheet" href="https://fonts.googleapis.com/css2?family=Open+Sans:wght@400;600;700&display=swap">
<style>
  :root {
    --ink: #1d1d1d;
    --teal: #25a796;
    --sand: #d7c38c;
    --paper: #fbfbfa;
    --rule: #d4d4d4;
    --backdrop: #ecebe7;
    --leaf-dark: #4f6b3a;
    --leaf-mid: #7f9a5c;
    --leaf-light: #c9d3b0;
  }
  * { box-sizing: border-box; margin: 0; padding: 0; }
  html, body {
    width: 1200px; height: 780px; overflow: hidden;
    background: var(--backdrop);
    font-family: "Open Sans", Arial, sans-serif;
  }
  .canvas {
    width: 1200px; height: 780px;
    display: flex; align-items: center; justify-content: center; gap: 30px;
  }
  .card {
    position: relative;
    width: 560px; height: 320px;
    border-radius: 18px;
    overflow: hidden;
    box-shadow: 0 6px 18px rgba(0,0,0,.18);
  }

  /* Front: logo + contact */
  .card--front { background: var(--paper); display: flex; }
  .brand-panel {
    width: 52%;
    display: flex; align-items: center; justify-content: center;
    border-right: 1px solid var(--rule);
    margin: 40px 0;
  }
  .brand-name {
    font-weight: 700; font-size: 30px; letter-spacing: 1px;
    text-transform: uppercase; color: var(--ink);
    text-align: center; line-height: 1.15;
  }
  .contact-panel {
    flex: 1;
    padding: 62px 26px 0 28px;
  }
  .person-name { font-weight: 700; font-size: 21px; color: var(--ink); }
  .person-role {
    margin-top: 4px;
    font-size: 13px; line-height: 1.35; color: var(--teal);
  }
  .contact-list { list-style: none; margin-top: 24px; }
  .contact-list li {
    display: flex; align-items: center; gap: 8px;
    font-size: 11.5px; color: var(--ink); margin-bottom: 7px;
  }
  .contact-icon {
    width: 17px; height: 17px; border-radius: 3px;
    background: var(--teal);
    display: flex; align-items: center; justify-content: center;
  }
  .social-row { display: flex; gap: 8px; margin-top: 14px; }
  .social-tile { width: 20px; height: 20px; border-radius: 3px; background: var(--sand); }

  /* Back: photo + logo panel */
  .card--back { background: var(--leaf-mid); }
  .photo-fill {
    position: absolute; inset: 0;
    background: linear-gradient(120deg, var(--leaf-light) 0%, var(--leaf-mid) 45%, var(--leaf-dark) 100%);
  }
  .logo-plate {
    position: absolute; right: 28px; bottom: 40px;
    width: 230px; height: 120px;
    background: rgba(255,255,255,.72);
    border-radius: 10px;
    display: flex; align-items: center; justify-content: center;
  }
  .logo-plate .brand-name { font-size: 22px; }
</style>
</head>
<body>
<main class="canvas">
  <section class="card card--front" aria-label="Card front">
    <div class="brand-panel">
      <p class="brand-name">Satchel &amp;<br>Sundial</p>
    </div>
    <div class="contact-panel">
      <h1 class="person-name">Dorota Falkner</h1>
      <p class="person-role">Your Lifestyle Business Coach,<br>Retreat &amp; Trip Leader</p>
      <ul class="contact-list">
        <li>
          <span class="contact-icon">
            <svg width="11" height="11" viewBox="0 0 12 12" fill="none" stroke="#fff" stroke-width="1.1">
              <circle cx="6" cy="6" r="5"/><ellipse cx="6" cy="6" rx="2.2" ry="5"/><line x1="1" y1="6" x2="11" y2="6"/>
            </svg>
          </span>
          http://satchelandsundial.example
        </li>
        <li>
          <span class="contact-icon">
            <svg width="11" height="9" viewBox="0 0 12 9" fill="none" stroke="#fff" stroke-width="1.1">
              <rect x="0.6" y="0.6" width="10.8" height="7.8"/><polyline points="0.6,0.6 6,5 11.4,0.6"/>
            </svg>
          </span>
          hello@satchelandsundial.example
        </li>
      </ul>
      <div class="social-row">
        <span class="social-tile"></span><span class="social-tile"></span><span class="social-tile"></span>
      </div>
    </div>
  </section>

  <section class="card card--back" aria-label="Card back">
    <div class="photo-fill" role="img" aria-label="Photo of the coach smiling among green trees and leaves, holding a hashtag sign"></div>
    <div class="logo-plate">
      <p class="brand-name">Satchel &amp;<br>Sundial</p>
    </div>
  </section>
</main>
</body>
</html>
```